Business Card - high end, modern health care

Hey designers!

We need a double sided business card for the boutique, cutting edge physical therapy rehabilitation centre in Sydney's Northern Beaches.

With the most qualified physios in the area The Harbourview Motion Clinic does what other physiotherapy practices do not, we take our time with our patients giving them longer appointments, better physios and therefor faster results!

We guarantee that the service people receive at THMC will be unparalleled.

Hence we need a business card to reflect our modern, boutique, high end service. The final design needs to reflect that we are in a class of our own yet with the feel of beachside retreat.

Below I have attached our logo in both blue on white and white on blue. The exact colour is;
and the font that we have used in our logo is Tex Gyre Aventador.

I like the idea of the blue as the main colour as it is more eye catching and our signage onto the main road will be in this blue and in the interest of consistency across marketing the blue needs to be a part of the design. However I would appreciate a few designs onto a wooden background as this is a visual theme within the fitout of the practice.

The design needs to be of standard size (91x55mm).

Target Market(s)

We target people who have an end outcome in mind and those who have had poor experiences with other providers and ensure that everyone gets the care that they deserve with a premium service that is tailored to the individuals circumstances. As a premium service, the target market is highly educated, business and tech savvy with the additional target market of elderly people who have self funded their retirement and see value in paying for the best ongoing rehabilitation to maintain independence.

Industry/Entity Type

Physical Therapy

Contact Information for Business Card

Name, designation( Titled Musculoskeletal Physiotherapist... there will also be those in the company that have multiple designations ie 5 or 6 words long), phone number, email, facebook, instagram, address

Font styles to use
Sans Serif

Colors

Designer to choose colors to be used in the design.

Requirements
Must have
• Front - The logo as large as possible, blue or wooden theme, and all of the important details.
• Back - A blank space/lines on which to write appointment times (no "Appointment, date, time" etc.)
Nice to have
• facebook url
• logos for facebook and instagram
• Mini logos for the phone and email?

```html
<!DOCTYPE html>
<html lang="en">
<head>
<meta charset="utf-8">
<title>The Harbourview Motion Clinic – Business Card</title>
<link rel="stylesheet" href="https://fonts.googleapis.com/css2?family=Raleway:wght@400;500;600;700&display=swap">
<style>
  :root {
    --stage: #4d5667;
    --brand-blue: #0e58a8;
    --wave-lilac: #8796cc;
    --paper: #ffffff;
    --ink: #1c1c1c;
    --rule: #555555;
    --dash: #b5b5b5;
    --social-blue: #2d8fd6;
    --social-pink: #e0609a;
  }
  * { margin: 0; padding: 0; box-sizing: border-box; }
  html, body { width: 1200px; height: 1000px; overflow: hidden; }
  body {
    background: var(--stage);
    font-family: "Raleway", Arial, sans-serif;
    position: relative;
  }
  .card {
    position: absolute;
    width: 658px;
    height: 375px;
    overflow: hidden;
    box-shadow: 0 6px 18px rgba(0,0,0,0.25);
  }
  .card-front { left: 136px; top: 78px; background: var(--brand-blue); }
  .card-back { left: 437px; top: 548px; background: var(--paper); }

  .front-wave { position: absolute; inset: 0; }

  .brand {
    position: absolute;
    display: flex;
    align-items: center;
    gap: 10px;
  }
  .brand-dot { border-radius: 50%; flex: none; }
  .brand-name {
    font-weight: 700;
    text-transform: uppercase;
    line-height: 1;
  }
  .brand-name .line-1 { display: block; letter-spacing: 0.5px; }
  .brand-name .line-2 { display: block; letter-spacing: 4.5px; margin-top: 4px; }

  .card-front .brand { left: 0; right: 0; top: 142px; justify-content: center; }
  .card-front .brand-dot { width: 58px; height: 58px; background: var(--paper); }
  .card-front .brand-name { color: var(--paper); }
  .card-front .line-1 { font-size: 30px; }
  .card-front .line-2 { font-size: 18px; }

  .card-back .brand { left: 0; right: 0; top: 63px; justify-content: center; }
  .card-back .brand-dot { width: 45px; height: 45px; background: var(--brand-blue); }
  .card-back .brand-name { color: var(--brand-blue); }
  .card-back .line-1 { font-size: 24px; }
  .card-back .line-2 { font-size: 14px; letter-spacing: 3.6px; margin-top: 3px; }

  .rule { position: absolute; left: 41px; width: 577px; border-top: 1.5px solid var(--rule); }
  .rule-top { top: 147px; }
  .rule-mid { top: 249px; }
  .rule-write { top: 338px; border-top: 1.5px dashed var(--dash); }

  .person { position: absolute; right: 410px; top: 174px; text-align: right; }
  .person-name { font-size: 25px; font-weight: 500; color: var(--ink); white-space: nowrap; }
  .person-name .accent { color: var(--brand-blue); }
  .person-role { font-size: 14px; color: var(--ink); margin-top: 7px; }

  .contact { position: absolute; left: 327px; top: 170px; list-style: none; }
  .contact li { display: flex; align-items: center; gap: 16px; font-size: 17px; color: var(--ink); height: 32px; white-space: nowrap; }
  .contact svg { width: 24px; height: 24px; flex: none; }

  .social { position: absolute; top: 270px; left: 51px; display: flex; gap: 44px; list-style: none; }
  .social li { display: flex; align-items: center; gap: 9px; font-size: 15px; color: var(--ink); white-space: nowrap; }
  .social .dot { width: 22px; height: 22px; border-radius: 50%; flex: none; }
  .dot-fb { background: var(--social-blue); }
  .dot-ig { background: var(--social-pink); }
</style>
</head>
<body>

  <section class="card card-front" aria-label="Business card front">
    <svg class="front-wave" viewBox="0 0 658 375" width="658" height="375" aria-hidden="true">
      <path d="M0,272 C150,330 250,310 380,260 S560,200 658,262 L658,375 L0,375 Z" fill="var(--wave-lilac)"/>
      <path d="M0,307 C120,345 250,340 380,288 S575,218 658,262 L658,375 L0,375 Z" fill="var(--paper)"/>
    </svg>
    <div class="brand">
      <span class="brand-dot"></span>
      <span class="brand-name">
        <span class="line-1">The Harbourview</span>
        <span class="line-2">Motion Clinic</span>
      </span>
    </div>
  </section>

  <section class="card card-back" aria-label="Business card back">
    <div class="brand">
      <span class="brand-dot"></span>
      <span class="brand-name">
        <span class="line-1">The Harbourview</span>
        <span class="line-2">Motion Clinic</span>
      </span>
    </div>

    <div class="rule rule-top"></div>

    <div class="person">
      <p class="person-name">Name of <span class="accent">Person</span></p>
      <p class="person-role">Designation</p>
    </div>

    <ul class="contact">
      <li>
        <svg viewBox="0 0 24 24" aria-hidden="true">
          <circle cx="12" cy="12" r="10.5" fill="none" stroke="var(--ink)" stroke-width="1.6"/>
          <path d="M8.3 7.2c.4-.4 1-.4 1.3 0l1.2 1.6c.3.4.2.9-.1 1.2l-.7.6c.5 1.2 1.4 2.2 2.6 2.8l.6-.7c.3-.3.8-.4 1.2-.1l1.6 1.1c.4.3.4.9.1 1.3l-.8.9c-.6.6-1.5.8-2.3.4-2.4-1.1-4.2-3-5.3-5.4-.3-.8-.1-1.7.5-2.300z" fill="var(--ink)"/>
        </svg>
        <span>555.018.4127</span>
      </li>
      <li>
        <svg viewBox="0 0 24 24" aria-hidden="true">
          <rect x="1.5" y="5" width="21" height="14" fill="var(--ink)"/>
          <path d="M2 5.8 L12 13 L22 5.8" fill="none" stroke="var(--paper)" stroke-width="1.4"/>
        </svg>
        <span>hello@harbourviewmotion.com</span>
      </li>
    </ul>

    <div class="rule rule-mid"></div>

    <ul class="social">
      <li><span class="dot dot-fb"></span><span>/harbourviewmotion</span></li>
      <li><span class="dot dot-ig"></span><span>@harbourview.motion</span></li>
    </ul>

    <div class="rule rule-write"></div>
  </section>

</body>
</html>
```